Folded A4 flyer for design&construction company

Folded A4 flyer needed. Keywords: elegant, stylish
our website www.dorvika.ae

Industry/Entity Type

Construction

```html
<!DOCTYPE html>
<html lang="en">
<head>
<meta charset="utf-8">
<title>Dorvika – Design &amp; Construction Flyer</title>
<link href="https://fonts.googleapis.com/css2?family=Raleway:wght@500&family=Open+Sans:wght@700&family=Dancing+Script:wght@600&display=swap" rel="stylesheet">
<style>
  :root {
    --stage: #8b8d87;
    --charcoal: #4a4a4c;
    --charcoal-deep: #3b3b3d;
    --slate: #5c5c5f;
    --gold: #c9a62c;
    --gold-light: #e2c760;
    --gold-dark: #9c7a14;
    --white: #ffffff;
  }
  * { box-sizing: border-box; margin: 0; padding: 0; }
  html, body {
    width: 1200px;
    height: 789px;
    overflow: hidden;
    background: var(--stage);
  }
  .flyer-cover {
    position: absolute;
    left: 338px;
    top: 24px;
    width: 524px;
    height: 740px;
    background: linear-gradient(180deg, var(--charcoal-deep) 0%, var(--charcoal) 100%);
    overflow: hidden;
  }
  .brand-header {
    position: absolute;
    left: 0; top: 0;
    width: 100%;
    height: 232px;
    text-align: center;
  }
  .brand-name {
    position: absolute;
    top: 92px;
    width: 100%;
    font-family: "Raleway", sans-serif;
    font-weight: 500;
    font-size: 64px;
    letter-spacing: 2px;
    color: var(--white);
    line-height: 1;
  }
  .brand-tagline {
    position: absolute;
    top: 168px;
    width: 100%;
    font-family: "Dancing Script", cursive;
    font-weight: 600;
    font-size: 22px;
    color: var(--gold);
    letter-spacing: 0.5px;
  }
  .hero-photo {
    position: absolute;
    left: 0; top: 232px;
    width: 100%;
    height: 344px;
    background:
      radial-gradient(ellipse 55% 30% at 62% 22%, #f6f3ea 0%, rgba(246,243,234,0) 70%),
      linear-gradient(180deg, #e3a823 0%, #f1e7cf 38%, #e9dcc2 50%, #c9953c 66%, #b07a2c 100%);
  }
  .hero-quote {
    position: absolute;
    left: 0; top: 520px;
    width: 100%;
    text-align: center;
    font-family: "Dancing Script", cursive;
    font-weight: 600;
    font-size: 25px;
    color: var(--white);
  }
  .gold-rule {
    position: absolute;
    left: 0; top: 576px;
    width: 100%;
    height: 26px;
  }
  .web-band {
    position: absolute;
    left: 0; top: 620px;
    width: 100%;
    height: 38px;
    background: linear-gradient(90deg, var(--gold-dark) 0%, var(--gold) 30%, var(--gold-light) 55%, var(--gold) 80%, var(--gold-dark) 100%);
    display: flex;
    align-items: center;
    justify-content: center;
  }
  .web-address {
    font-family: "Open Sans", sans-serif;
    font-weight: 700;
    font-size: 19px;
    letter-spacing: 0.5px;
    color: var(--white);
  }
  .cover-footer {
    position: absolute;
    left: 0; top: 658px;
    width: 100%;
    height: 82px;
    background: var(--charcoal-deep);
  }
</style>
</head>
<body>
  <main class="flyer-cover">
    <header class="brand-header">
      <h1 class="brand-name">DORVIKA</h1>
      <p class="brand-tagline">design &amp; construction</p>
    </header>

    <div class="hero-photo" role="img" aria-label="Photograph of a modern lounge interior with a curved yellow ceiling, a floating white staircase, black lounge chairs and a polished wooden floor"></div>
    <p class="hero-quote">Quality is not an act, it is a habit - Helena Marsh</p>

    <svg class="gold-rule" viewBox="0 0 524 26" preserveAspectRatio="none" aria-hidden="true">
      <rect x="0" y="0" width="524" height="26" fill="var(--slate)"/>
      <polygon points="0,18 524,6 524,14 0,26" fill="var(--gold)"/>
    </svg>

    <div class="web-band">
      <span class="web-address">WWW.DORVIKA.AE</span>
    </div>

    <footer class="cover-footer"></footer>
  </main>
</body>
</html>
```